Business card design and logo for hot water plumbing business

I need a logo and business card for my business which installs hot water heaters
Must have on front:
Bramblefield Hot Water Solutions
Gareth Pennick
0417382946

Either front or back:
gareth@bramblefieldhotwatersolutions.com.au
ABN 48276153094
Licence No 583214K

On the back in point form:
Supply and installation of
• electric storage
• gas storage/instantaneous
• heat pumps
• solar heaters

Iv provided 3 examples of cards I like but open to different ideas.

```html
<!DOCTYPE html>
<html lang="en">
<head>
<meta charset="utf-8">
<title>Bramblefield Hot Water Solutions – Business Card</title>
<link rel="stylesheet" href="https://fonts.googleapis.com/css2?family=Open+Sans:wght@400;600;700;800&display=swap">
<style>
  :root {
    --bg: #e9eaec;
    --card: #ffffff;
    --blue: #1a56a8;
    --orange: #f06a1f;
    --ink: #4a4d52;
    --rule: #c9ccd1;
  }
  * { margin: 0; padding: 0; box-sizing: border-box; }
  html, body { width: 1200px; height: 899px; overflow: hidden; }
  body {
    background: var(--bg);
    font-family: "Open Sans", Arial, sans-serif;
    position: relative;
  }
  .card {
    position: absolute;
    top: 290px;
    width: 540px;
    height: 310px;
    background: var(--card);
    border-radius: 34px;
    overflow: hidden;
    box-shadow: 0 6px 18px rgba(0,0,0,0.12);
  }
  .card--front { left: 40px; }
  .card--back { left: 620px; }

  .card__band { position: absolute; inset: 0; width: 100%; height: 100%; }

  .brand {
    position: absolute;
    text-align: center;
    color: var(--blue);
    font-weight: 800;
    line-height: 1.1;
  }
  .brand__dot {
    display: block;
    margin: 0 auto 8px;
    border-radius: 50%;
    background: var(--orange);
  }
  .card--front .brand { left: 18px; top: 44px; width: 204px; font-size: 16px; }
  .card--front .brand__dot { width: 34px; height: 34px; }
  .card--back .brand { left: 0; right: 0; top: 40px; font-size: 24px; }
  .card--back .brand__dot { width: 44px; height: 44px; margin-bottom: 10px; }

  .divider {
    position: absolute;
    left: 232px; top: 30px;
    width: 1px; height: 150px;
    background: var(--rule);
  }
  .contact {
    position: absolute;
    left: 246px; top: 28px;
    right: 14px;
    color: var(--ink);
    font-size: 10.5px;
    line-height: 1.45;
    white-space: nowrap;
  }
  .contact__name { color: var(--blue); font-weight: 700; font-size: 13.5px; line-height: 1.3; }
  .contact__role { font-size: 12px; margin-bottom: 5px; }
  .contact__address { margin-bottom: 3px; }
  .contact__row { display: flex; align-items: center; gap: 5px; }
  .contact__row svg { width: 10px; height: 10px; fill: var(--blue); flex: none; }

  .services {
    position: absolute;
    left: 0; right: 0; top: 178px;
    text-align: center;
    color: var(--ink);
    font-size: 12px;
    line-height: 1.5;
  }
  .services__title { color: var(--blue); font-weight: 700; font-size: 12.5px; margin-bottom: 2px; }
  .services__list { list-style: none; display: inline-block; text-align: left; }
  .services__list li::before { content: "• "; color: var(--orange); font-weight: 700; }
</style>
</head>
<body>

<section class="card card--front" aria-label="Card front">
  <svg class="card__band" viewBox="0 0 540 310" preserveAspectRatio="none" aria-hidden="true">
    <path d="M0 175 C 170 188, 360 235, 500 310 L 0 310 Z" fill="var(--blue)"/>
    <path d="M0 168 C 178 180, 372 228, 512 310" fill="none" stroke="var(--orange)" stroke-width="3"/>
  </svg>

  <div class="brand">
    <span class="brand__dot"></span>
    Bramblefield Hot Water<br>Solutions
  </div>

  <div class="divider"></div>

  <div class="contact">
    <p class="contact__name">Gareth Pennick</p>
    <p class="contact__role">Consultant</p>
    <p class="contact__address">27 Kestrel Lane, Harwick NSW</p>
    <p class="contact__row">
      <svg viewBox="0 0 24 24"><path d="M6.6 10.8a15 15 0 0 0 6.6 6.6l2.2-2.2a1 1 0 0 1 1-.25 11.4 11.4 0 0 0 3.6.57 1 1 0 0 1 1 1V20a1 1 0 0 1-1 1A17 17 0 0 1 3 4a1 1 0 0 1 1-1h3.5a1 1 0 0 1 1 1c0 1.25.2 2.45.57 3.6a1 1 0 0 1-.25 1z"/></svg>
      0417382946
    </p>
    <p class="contact__row">
      <svg viewBox="0 0 24 24"><path d="M2 5h20v14H2z M2 5l10 8 10-8"/></svg>
      gareth@bramblefieldhotwatersolutions.com.au
    </p>
    <p>www.bramblefieldhotwater.com.au</p>
    <p>ABN 48276153094 &nbsp;·&nbsp; Licence No 583214K</p>
  </div>
</section>

<section class="card card--back" aria-label="Card back">
  <div class="brand">
    <span class="brand__dot"></span>
    Bramblefield Hot Water<br>Solutions
  </div>
  <div class="services">
    <p class="services__title">Supply and installation of</p>
    <ul class="services__list">
      <li>electric storage</li>
      <li>gas storage/instantaneous</li>
      <li>heat pumps</li>
      <li>solar heaters</li>
    </ul>
  </div>
</section>

</body>
</html>
```